The book is called "Distance Racing Blueprints: An In-Depth Manual for Achieving Your Peak Race Day - Featuring Schedules, Counsel and Target-Reaching Pointers "

It is a 6" x 9" book with 205 pages. This is an advanced book for runners who have been running and trying to hit their marathon goals, but haven't been able to do so. This needs to portray a professional coaching image and high performing athlete.

I have running photos of myself running marathons if you thought that was the route to take, but I'm open to your creative influence.

```html
<!DOCTYPE html>
<html lang="en">
<head>
<meta charset="utf-8">
<title>Distance Racing Blueprints — Cover</title>
<link rel="stylesheet" href="https://fonts.googleapis.com/css2?family=Oswald:wght@500;600&family=Encode+Sans+Condensed:wght@300;400&display=swap">
<style>
  :root {
    --cover-bg: #333233;
    --ink-light: #f2f2f2;
    --ink-soft: #d9d9d9;
    --photo-light: #8a8a88;
    --photo-dark: #4a4a48;
  }
  html, body {
    margin: 0;
    padding: 0;
    width: 800px;
    height: 1200px;
    overflow: hidden;
    background: var(--cover-bg);
  }
  .cover {
    position: relative;
    width: 800px;
    height: 1200px;
    background: var(--cover-bg);
  }
  .author-name {
    position: absolute;
    top: 46px;
    left: 0;
    width: 100%;
    text-align: center;
    font-family: "Encode Sans Condensed", sans-serif;
    font-weight: 300;
    font-size: 23px;
    letter-spacing: 0.22em;
    color: var(--ink-soft);
    margin: 0;
  }
  .title-art {
    position: absolute;
    top: 0;
    left: 0;
    width: 800px;
    height: 520px;
  }
  .race-photo {
    position: absolute;
    left: 148px;
    top: 544px;
    width: 512px;
    height: 512px;
    border-radius: 50%;
    background: radial-gradient(circle at 50% 40%, var(--photo-light) 0%, #6b6b69 55%, var(--photo-dark) 100%);
  }
  .tagline {
    position: absolute;
    top: 1116px;
    left: 0;
    width: 100%;
    text-align: center;
    font-family: "Encode Sans Condensed", sans-serif;
    font-weight: 400;
    font-size: 20px;
    letter-spacing: 0.06em;
    color: var(--ink-soft);
    margin: 0;
  }
</style>
</head>
<body>
  <main class="cover">
    <p class="author-name">AUTHORS NAME</p>

    <svg class="title-art" viewBox="0 0 800 520" xmlns="http://www.w3.org/2000/svg">
      <defs>
        <linearGradient id="title-fill" x1="0" y1="0" x2="1" y2="0">
          <stop offset="0" stop-color="#ffffff"/>
          <stop offset="0.2" stop-color="#9a9a9a"/>
          <stop offset="0.35" stop-color="#f5f5f5"/>
          <stop offset="0.5" stop-color="#b0b0b0"/>
          <stop offset="0.65" stop-color="#ffffff"/>
          <stop offset="0.85" stop-color="#8c8c8c"/>
          <stop offset="1" stop-color="#e6e6e6"/>
        </linearGradient>
        <linearGradient id="reflection-fade" x1="0" y1="0" x2="0" y2="1">
          <stop offset="0" stop-color="#fff" stop-opacity="0.75"/>
          <stop offset="1" stop-color="#fff" stop-opacity="0"/>
        </linearGradient>
        <mask id="reflection-mask" maskUnits="userSpaceOnUse" x="0" y="292" width="800" height="80">
          <rect x="0" y="292" width="800" height="80" fill="url(#reflection-fade)"/>
        </mask>
      </defs>

      <g class="main-title">
        <text x="99" y="292" textLength="610" lengthAdjust="spacingAndGlyphs"
              font-family="Oswald, sans-serif" font-weight="600" font-size="165"
              fill="url(#title-fill)">DISTANCE</text>
      </g>

      <g class="main-title-reflection" mask="url(#reflection-mask)">
        <text x="99" y="292" textLength="610" lengthAdjust="spacingAndGlyphs"
              font-family="Oswald, sans-serif" font-weight="600" font-size="165"
              fill="url(#title-fill)" transform="translate(0 584) scale(1 -1)">DISTANCE</text>
      </g>

      <text class="subtitle" x="100" y="486" textLength="600" lengthAdjust="spacingAndGlyphs"
            font-family="Oswald, sans-serif" font-weight="500" font-size="50"
            letter-spacing="4" fill="#f2f2f2">RACING BLUEPRINTS</text>
    </svg>

    <div class="race-photo" role="img" aria-label="Photo of a runner's legs and bright running shoes climbing concrete steps"></div>

    <p class="tagline">FEATURING SCHEDULES, COUNSEL &amp; TARGET-REACHING POINTERS</p>
  </main>
</body>
</html>
```